SkyvornQ Business Cards and Stationary Design

Need a design for our business cards and stationary. I want to carry on the theme of the logo. I want the business cards to have a design on the back. I would like the business cards and the stationary to carry the same theme, design scheme, and branding

Target Market(s)

Airlines and Maintenance Facilities

Industry/Entity Type

Aviation

Contact Information for Business Card

Name
Position Title
Address: 4827 Trellis Hollow Road, Fort Pierce, Florida, 34951
Office Number
Mobile Number
Email
Website

Font styles to use
Serif
Sans Serif

Colors

Designer to choose colors to be used in the design.

```html
<!DOCTYPE html>
<html lang="en">
<head>
<meta charset="utf-8">
<title>SkyvornQ Business Card</title>
<link href="https://fonts.googleapis.com/css2?family=Work+Sans:wght@400;500&display=swap" rel="stylesheet">
<style>
  :root {
    --page-bg: #2a2a2b;
    --card-bg: #1c1c1d;
    --card-edge: #232324;
    --ink-white: #f4f4f4;
    --ink-soft: #d9d9d9;
    --ink-silver: #b9b9bb;
    --accent-blue: #1f9be0;
  }
  * { box-sizing: border-box; margin: 0; padding: 0; }
  html, body {
    width: 1200px; height: 900px; overflow: hidden;
    background: var(--page-bg);
    font-family: "Work Sans", Arial, sans-serif;
  }
  .canvas { position: relative; width: 1200px; height: 900px; }
  .card {
    position: absolute; left: 290px; width: 620px; height: 354px;
    background: linear-gradient(135deg, var(--card-edge), var(--card-bg) 60%);
    box-shadow: 0 6px 18px rgba(0,0,0,.45);
  }
  .card--back { top: 70px; display: flex; align-items: center; justify-content: center; }
  .card--front { top: 476px; }

  .brand { display: flex; align-items: center; gap: 12px; }
  .brand__mark {
    width: 18px; height: 18px; flex: none;
    background: var(--ink-silver);
  }
  .brand__name {
    font-weight: 500; font-size: 40px; letter-spacing: 0;
    color: var(--ink-silver); line-height: 1;
  }
  .card--front .brand {
    position: absolute; left: 0; top: 154px; width: 352px; justify-content: center;
  }
  .card--front .brand__mark { width: 16px; height: 16px; background: var(--ink-white); }
  .card--front .brand__name { font-size: 36px; color: var(--ink-white); }

  .divider {
    position: absolute; left: 352px; top: 92px; width: 2px; height: 170px;
    background: var(--ink-soft);
  }
  .contact { position: absolute; left: 382px; top: 92px; color: var(--ink-white); }
  .contact__name {
    font-weight: 500; font-size: 25px; letter-spacing: 2px;
    color: var(--accent-blue); text-transform: uppercase; line-height: 1;
  }
  .contact__title { font-size: 15px; color: var(--ink-soft); margin-top: 4px; }
  .contact__address { font-size: 14px; line-height: 1.4; margin-top: 14px; letter-spacing: .5px; }
  .contact__list { list-style: none; margin-top: 10px; }
  .contact__item {
    display: flex; align-items: center; gap: 10px;
    font-size: 15px; line-height: 1.45; letter-spacing: .5px;
  }
  .contact__item svg { width: 11px; height: 11px; flex: none; }
  .contact__highlight { color: var(--accent-blue); }
</style>
</head>
<body>
<main class="canvas">
  <section class="card card--back" aria-label="Card back">
    <div class="brand">
      <span class="brand__mark"></span>
      <span class="brand__name">SkyvornQ</span>
    </div>
  </section>

  <section class="card card--front" aria-label="Card front">
    <div class="brand">
      <span class="brand__mark"></span>
      <span class="brand__name">SkyvornQ</span>
    </div>
    <span class="divider"></span>
    <div class="contact">
      <p class="contact__name">Dorian Vale</p>
      <p class="contact__title">Director</p>
      <p class="contact__address">4827 Trellis Hollow Road,<br>Fort Pierce, Florida, 34951</p>
      <ul class="contact__list">
        <li class="contact__item">
          <svg viewBox="0 0 12 12"><path d="M2.5 1h2l1 3-1.3 1a6 6 0 0 0 2.8 2.8l1-1.3 3 1v2a1.5 1.5 0 0 1-1.5 1.5A9.5 9.5 0 0 1 1 2.5 1.5 1.5 0 0 1 2.5 1z" fill="var(--accent-blue)"/></svg>
          513-555-0182
        </li>
        <li class="contact__item">
          <svg viewBox="0 0 12 12"><rect x="1" y="2.5" width="10" height="7" fill="none" stroke="var(--accent-blue)" stroke-width="1.2"/><path d="M1 2.5l5 4 5-4" fill="none" stroke="var(--accent-blue)" stroke-width="1.2"/></svg>
          info@skyvornq.com
        </li>
        <li class="contact__item">
          <svg viewBox="0 0 12 12"><circle cx="6" cy="6" r="5" fill="none" stroke="var(--accent-blue)" stroke-width="1.2"/><path d="M1 6h10M6 1c-2.5 3-2.5 7 0 10M6 1c2.5 3 2.5 7 0 10" fill="none" stroke="var(--accent-blue)" stroke-width="1"/></svg>
          <span>www.<span class="contact__highlight">skyvornq</span>.com</span>
        </li>
      </ul>
    </div>
  </section>
</main>
</body>
</html>
```